New tech executive consulting company needs professionally branded document templates

We are a new business selling fractional board advisory and go-to-market consulting services into the Technology space. Tessaly Brink are experts in providing high-quality executive-level leaders on a part-time basis to tech companies in need of their expertise. We work closely with clients to understand their business needs, challenges, and goals, and provides customised solutions to help them succeed. Due to our audience we need the design to have a high quality, executive look and feel.

Our first website is live and can be found at tessalybrink.example. We also already have a logo which I've uploaded. Our brand is clean and uses orange to give it colour and an identity that stands out.

We need some document master templates created so we can create our own presentations (Google Slides & Powerpoint), PDF documents, and Word templates, and ideally also a LinkedIn banner.

```html
<!DOCTYPE html>
<html lang="en">
<head>
<meta charset="utf-8">
<title>Tessaly Brink – Presentation Template</title>
<link href="https://fonts.googleapis.com/css2?family=Poppins:wght@400;500;600;700&family=IBM+Plex+Sans:wght@600&family=Fira+Sans:ital,wght@1,400&display=swap" rel="stylesheet">
<style>
  :root {
    --ink: #2a3340;
    --orange: #ec8550;
    --white: #ffffff;
    --canvas: #8e8e8e;
    --text: #2b2b2b;
  }
  * { box-sizing: border-box; margin: 0; padding: 0; }
  html, body { width: 1200px; height: 4231px; overflow: hidden; background: var(--canvas); }
  body { position: relative; font-family: "Poppins", sans-serif; color: var(--text); }

  .slide { position: absolute; left: 59px; width: 1080px; height: 607px; overflow: hidden; background: var(--white); }
  .slide > svg.shapes { position: absolute; inset: 0; width: 1080px; height: 607px; }
  .photo { position: absolute; }
  .accent-bar { position: absolute; left: 0; width: 11px; background: var(--orange); }

  .wordmark { position: absolute; color: var(--white); font-family: "Poppins", sans-serif; font-weight: 600; letter-spacing: 3px; text-align: right; line-height: 1.1; }

  /* Cover */
  .cover { top: 84px; }
  .cover .photo { inset: 0; background: linear-gradient(160deg, #c9d4dc 0%, #8d9aa6 40%, #3d4a57 80%); }
  .cover .wordmark { right: 75px; top: 158px; font-size: 40px; }
  .cover .tagline { position: absolute; right: 75px; top: 312px; text-align: right; font-family: "IBM Plex Sans", sans-serif; font-weight: 600; font-size: 35px; line-height: 53px; color: var(--white); }
  .cover .tagline .hl { color: var(--orange); }

  /* Agenda */
  .agenda { top: 762px; }
  .agenda .accent-bar { top: 176px; height: 256px; }
  .agenda .title { position: absolute; left: 70px; top: 400px; font-size: 37px; font-weight: 700; color: var(--ink); letter-spacing: 1px; }
  .agenda .item { position: absolute; font-size: 22px; font-weight: 500; color: var(--ink); }

  /* About */
  .about { top: 1448px; }
  .about .photo { left: 440px; top: 0; width: 640px; height: 607px; background: linear-gradient(90deg, #ffffff 0%, rgba(255,255,255,0) 30%), linear-gradient(150deg, #d9dde1 0%, #9aa3ab 45%, #4a525c 100%); }
  .about .accent-bar { top: 174px; height: 172px; }
  .about .eyebrow { position: absolute; left: 51px; top: 86px; font-size: 23px; font-weight: 600; color: var(--orange); }
  .about .heading { position: absolute; left: 51px; top: 128px; width: 420px; font-size: 25px; font-weight: 600; line-height: 42px; color: #1f1f1f; }
  .about .body { position: absolute; left: 51px; top: 248px; width: 423px; font-size: 12.5px; line-height: 21px; text-align: justify; color: #333; }
  .about .body p + p { margin-top: 21px; }

  /* Profile */
  .profile { top: 2139px; }
  .profile .accent-bar { top: 176px; height: 254px; }
  .profile .photo { left: 70px; top: 98px; width: 426px; height: 432px; background: radial-gradient(circle at 50% 45%, #c9a48c 0%, #8a6a55 35%, #3f4f6b 70%, #2d3b55 100%); }
  .profile .brand-box { position: absolute; left: 622px; top: 0; width: 458px; height: 192px; background: var(--ink); }
  .profile .wordmark { right: 62px; top: 42px; font-size: 40px; }
  .profile .name { position: absolute; left: 622px; top: 262px; font-size: 27px; font-weight: 700; color: #1a1a1a; }
  .profile .bio { position: absolute; left: 622px; top: 340px; width: 405px; font-size: 11.5px; line-height: 23px; text-align: justify; color: #333; }
  .profile .bio p + p { margin-top: 23px; }

  /* Contact */
  .contact { top: 2842px; }
  .contact .accent-bar { top: 175px; height: 255px; }
  .contact .title { position: absolute; left: 70px; top: 66px; font-size: 39px; font-weight: 700; color: var(--ink); letter-spacing: 1px; }
  .contact .lead { position: absolute; left: 70px; top: 145px; font-size: 15px; font-weight: 600; line-height: 28px; color: #1f1f1f; }
  .contact .badge-label { position: absolute; left: 353px; top: 310px; width: 200px; text-align: center; font-size: 36px; line-height: 46px; color: var(--white); font-weight: 400; }
  .contact .row { position: absolute; right: 222px; font-size: 22px; font-weight: 600; color: var(--white); text-align: right; }

  /* Closing */
  .closing { top: 3538px; background: linear-gradient(135deg, #3a4350 0%, #232b37 55%, #1c232e 100%); }
  .closing .wordmark { left: 0; right: 0; top: 72px; text-align: center; font-size: 44px; }
  .closing .rule { position: absolute; left: 400px; width: 283px; height: 3px; background: var(--white); }
  .closing .thanks { position: absolute; left: 0; right: 0; top: 272px; text-align: center; font-family: "Fira Sans", sans-serif; font-style: italic; font-size: 54px; color: var(--white); }
  .closing .url { position: absolute; left: 0; right: 0; top: 536px; text-align: center; font-size: 21px; color: var(--white); }
</style>
</head>
<body>

<section class="slide cover">
  <div class="photo" role="img" aria-label="Two smiling colleagues in a bright glass-walled meeting room"></div>
  <svg class="shapes" viewBox="0 0 1080 607" aria-hidden="true">
    <polygon points="740,0 1080,0 1080,607 433,607" fill="var(--ink)"/>
    <polygon points="711,74 734,74 396,535 373,535" fill="var(--orange)"/>
    <polygon points="1080,541 1080,607 1033,607" fill="var(--orange)"/>
  </svg>
  <div class="wordmark">TESSALY<br>BRINK</div>
  <div class="tagline">Experts in providing<br><span class="hl">executive leadership</span><br>on demand</div>
</section>

<section class="slide agenda">
  <div class="accent-bar"></div>
  <svg class="shapes" viewBox="0 0 1080 607" aria-hidden="true">
    <defs>
      <linearGradient id="agendaBand" x1="0" y1="0" x2="1" y2="1">
        <stop offset="0" stop-color="#3a4451"/>
        <stop offset="1" stop-color="#1f2733"/>
      </linearGradient>
    </defs>
    <polygon points="39,0 277,0 680,607 441,607" fill="url(#agendaBand)" role="img" aria-label="Dimmed photo of a team working at a table"/>
    <line x1="39" y1="0" x2="441" y2="607" stroke="var(--orange)" stroke-width="4"/>
    <line x1="277" y1="0" x2="680" y2="607" stroke="var(--orange)" stroke-width="4"/>
    <!-- home -->
    <g fill="var(--white)">
      <polygon points="241,98 219,118 225,118 225,136 236,136 236,125 246,125 246,136 257,136 257,118 263,118"/>
    </g>
    <!-- info -->
    <circle cx="318" cy="235" r="20" fill="var(--white)"/>
    <circle cx="319" cy="226" r="3" fill="var(--ink)"/>
    <rect x="315" y="232" width="7" height="15" rx="1" fill="var(--ink)"/>
    <!-- user -->
    <circle cx="400" cy="363" r="20" fill="var(--white)"/>
    <circle cx="400" cy="356" r="7" fill="var(--ink)"/>
    <path d="M387,375 a13,11 0 0 1 26,0 z" fill="var(--ink)"/>
    <!-- phone + mail -->
    <g transform="translate(474,483)" fill="var(--white)">
      <path d="M-22,-12 q-4,14 10,26 l6,-6 -6,-7 -4,3 q-6,-6 -6,-12 l4,-2 -3,-8 z"/>
      <rect x="-6" y="-14" width="28" height="20" rx="2"/>
      <polyline points="-5,-13 8,-2 21,-13" fill="none" stroke="var(--ink)" stroke-width="2"/>
    </g>
  </svg>
  <div class="item" style="left:455px; top:102px;">Home</div>
  <div class="item" style="left:520px; top:220px;">About</div>
  <div class="item" style="left:592px; top:348px;">Rowan Pell</div>
  <div class="item" style="left:661px; top:468px;">Contact</div>
  <div class="title">AGENDA</div>
</section>

<section class="slide about">
  <svg class="shapes" viewBox="0 0 1080 607" aria-hidden="true">
    <polygon points="420,230 520,230 300,607 200,607" fill="var(--orange)" opacity="0.07"/>
  </svg>
  <div class="photo" role="img" aria-label="Two consultants smiling and pointing at a computer screen in an office"></div>
  <div class="accent-bar"></div>
  <div class="eyebrow">ABOUT US</div>
  <div class="heading">The smart way to scale your business</div>
  <div class="body">
    <p>Tessaly Brink are experts in providing high-quality executive-level leaders on a part-time basis to tech companies in need of their expertise. We work closely with clients to understand their business needs, challenges, and goals, and provides customised solutions to help them succeed.</p>
    <p>Our strategic insights, leadership, and collaborative approach make us a valuable partner for companies looking to drive growth and innovation. We are passionate about helping companies achieve their goals and are committed to providing the highest level of service to our clients.</p>
  </div>
</section>

<section class="slide profile">
  <div class="accent-bar"></div>
  <div class="photo" role="img" aria-label="Portrait of the founder in a blue blazer"></div>
  <div class="brand-box"><div class="wordmark">TESSALY<br>BRINK</div></div>
  <div class="name">ROWAN PELL</div>
  <div class="bio">
    <p>Rowan Pell is a highly accomplished business leader with extensive experience in executive-level leadership and strategy. As the founder of Tessaly Brink, Rowan brings his years of experience in the technology industry to help companies achieve their goals.</p>
    <p>Throughout his career, Rowan has held executive positions in companies ranging from startups to large corporations. He has a deep understanding of the tech industry and has helped companies at all stages of maturity drive significant growth and innovation.</p>
  </div>
</section>

<section class="slide contact">
  <div class="accent-bar"></div>
  <svg class="shapes" viewBox="0 0 1080 607" aria-hidden="true">
    <polygon points="630,0 1080,0 1080,607 0,607 0,576 258,576" fill="var(--ink)"/>
    <polygon points="671,31 1080,31 1080,576 305,576" fill="var(--orange)"/>
    <circle cx="453" cy="318" r="123" fill="var(--ink)"/>
    <circle cx="453" cy="258" r="47" fill="none" stroke="var(--white)" stroke-width="3"/>
    <g transform="translate(453,258)" fill="none" stroke="var(--white)" stroke-width="3">
      <rect x="-22" y="-16" width="44" height="30" rx="2"/>
      <polyline points="-22,-16 0,2 22,-16"/>
    </g>
    <g fill="none" stroke="var(--white)" stroke-width="1.5" stroke-dasharray="4 3">
      <circle cx="939" cy="167" r="33"/>
      <circle cx="939" cy="300" r="33"/>
      <circle cx="939" cy="433" r="33"/>
    </g>
    <path d="M927,155 q-4,16 12,26 l5,-5 -6,-6 -4,3 q-6,-5 -6,-11 l4,-2 -3,-7 z" fill="none" stroke="var(--white)" stroke-width="2"/>
    <circle cx="939" cy="300" r="13" fill="none" stroke="var(--white)" stroke-width="2"/>
    <g transform="translate(939,433)" fill="none" stroke="var(--white)" stroke-width="2">
      <rect x="-14" y="-9" width="28" height="19" rx="2"/>
      <polyline points="-14,-9 0,3 14,-9"/>
    </g>
  </svg>
  <div class="title">CONTACT US</div>
  <div class="lead">Let us help you take your business to the next level.<br>Contact us for a free consultation.</div>
  <div class="badge-label">Contact<br>Us</div>
  <div class="row" style="top:152px;">+44 7700 900123</div>
  <div class="row" style="top:285px;">Rowan Pell</div>
  <div class="row" style="top:418px;">info@tessalybrink.example</div>
</section>

<section class="slide closing" role="img" aria-label="Dark toned photo of colleagues collaborating">
  <div class="wordmark">TESSALY<br>BRINK</div>
  <div class="rule" style="top:257px;"></div>
  <div class="thanks">Thank You!</div>
  <div class="rule" style="top:354px;"></div>
  <div class="url">www.tessalybrink.example</div>
</section>

</body>
</html>
```